Varnex Consulting Business card design.

See our website www.varnexconsulting.example which will give you a good idea of what we are about. The font is called 'Play'.

I'd like a standout business card in keeping with the themes and branding on the website

Target Market(s)

professionals. HR directors

Industry/Entity Type

Business

Contact Information for Business Card

Varnex Consulting PO Box 3172 Merrowdale NSW 2291 1300 485 193 Gavin Threlkeld Principal email: career@varnexconsulting.example ABN: 71203948865

Font styles to use
Other font styles liked:
• Play

Requirements
Must have
• Must have same design colours and branding as website.
• On back I'd prefer a list of the things we do which appears below the name at the header on the website

```html
<!DOCTYPE html>
<html lang="en">
<head>
<meta charset="utf-8">
<title>Varnex Consulting – Business Card</title>
<link href="https://fonts.googleapis.com/css2?family=Play:wght@400;700&display=swap" rel="stylesheet">
<style>
  :root {
    --navy: #13293d;
    --blue: #2a96de;
    --paper: #f7f7f7;
    --ink: #13293d;
    --backdrop: #b3b0b0;
  }
  * { margin: 0; padding: 0; box-sizing: border-box; }
  html, body {
    width: 1200px; height: 1200px; overflow: hidden;
    background: var(--backdrop);
    font-family: "Play", sans-serif;
  }
  .card {
    position: absolute;
    left: 243px;
    width: 714px;
    height: 420px;
    overflow: hidden;
  }
  .card--front { top: 120px; background: var(--navy); }
  .card--back { top: 650px; background: var(--paper); }

  .brand {
    position: absolute; left: 0; right: 0;
    text-align: center;
    font-size: 60px; font-weight: 400;
    letter-spacing: 1px;
    line-height: 1;
    white-space: nowrap;
  }
  .card--front .brand { top: 133px; color: #ffffff; }
  .card--back .brand { top: 66px; color: var(--navy); }

  .services {
    position: absolute; left: 0; right: 0;
    text-align: center;
    font-size: 15px; letter-spacing: 2.4px;
    color: var(--blue);
    white-space: nowrap;
  }
  .card--front .services { top: 206px; }
  .card--back .services { top: 133px; }
  .services .sep { color: inherit; margin: 0 3px; }

  .web-line {
    position: absolute; left: 0; right: 0; top: 348px;
    display: flex; align-items: center; justify-content: center; gap: 12px;
    font-size: 19px; color: #ffffff;
  }
  .web-line .dash { width: 34px; height: 2px; background: var(--blue); border-radius: 2px; }
  .hl { color: var(--blue); }

  .person { position: absolute; left: 40px; top: 216px; color: var(--ink); }
  .person .name { font-size: 25px; font-weight: 700; }
  .person .role { font-size: 17px; margin-top: 6px; }

  .contacts { position: absolute; left: 332px; top: 218px; color: var(--ink); font-size: 19px; }
  .contacts .row { display: flex; align-items: center; height: 27.5px; }
  .contacts .icon { width: 18px; height: 18px; margin-right: 18px; }
  .contacts .meta { margin-top: 4px; line-height: 28px; }
  .contacts .label { color: var(--blue); }

  .band { position: absolute; left: 0; bottom: 0; width: 714px; height: 20px; }
</style>
</head>
<body>
  <section class="card card--front">
    <div class="brand">VARNEX CONSULTING</div>
    <div class="services">Search &amp; Select<span class="sep">I</span>Career<span class="sep">I</span>Coaching<span class="sep">I</span>Leadership<span class="sep">I</span>Outplacement</div>
    <div class="web-line"><span class="dash"></span><span>www.<span class="hl">varnexconsulting</span>.example</span><span class="dash"></span></div>
  </section>

  <section class="card card--back">
    <div class="brand">VARNEX CONSULTING</div>
    <div class="services">Search &amp; Select<span class="sep">I</span>Career<span class="sep">I</span>Coaching<span class="sep">I</span>Leadership<span class="sep">I</span>Outplacement</div>

    <div class="person">
      <div class="name">Gavin Threlkeld</div>
      <div class="role">Principal</div>
    </div>

    <div class="contacts">
      <div class="row">
        <svg class="icon" viewBox="0 0 20 20" aria-hidden="true"><path fill="#2a96de" d="M2 7c0-3 3-4 8-4s8 1 8 4v1h-4V6.5H6V8H2z"/><path fill="#2a96de" d="M5 9h10l2 8H3z"/><circle cx="10" cy="13" r="2" fill="#f7f7f7"/></svg>
        <span>1300 485 193</span>
      </div>
      <div class="row">
        <svg class="icon" viewBox="0 0 20 20" aria-hidden="true" fill="none" stroke="#2a96de" stroke-width="1.6"><circle cx="10" cy="10" r="8"/><ellipse cx="10" cy="10" rx="3.5" ry="8"/><path d="M2 10h16M3.5 6h13M3.5 14h13"/></svg>
        <span>www.<span class="hl">varnexconsulting</span>.example</span>
      </div>
      <div class="row">
        <svg class="icon" viewBox="0 0 20 20" aria-hidden="true"><rect x="1" y="4" width="18" height="12" fill="#2a96de"/><path d="M1.5 4.5L10 11l8.5-6.5M1.5 15.5l6-5M18.5 15.5l-6-5" stroke="#f7f7f7" stroke-width="1.3" fill="none"/></svg>
        <span>career@varnexconsulting.example</span>
      </div>
      <div class="meta">
        <div><span class="label">ABN:</span> 71203948865</div>
        <div>PO Box 3172 Merrowdale NSW 2291</div>
      </div>
    </div>

    <svg class="band" viewBox="0 0 714 20" preserveAspectRatio="none" aria-hidden="true">
      <polygon points="0,0 500,0 468,20 0,20" fill="#13293d"/>
      <polygon points="500,0 714,0 714,20 468,20" fill="#2a96de"/>
      <polygon points="500,0 507,0 475,20 468,20" fill="#f7f7f7"/>
    </svg>
  </section>
</body>
</html>
```